Harborview Estates Business Card for Apartment Buildings

Create business cards for resident managers who run apartment buildings. The audience is the public who are searching for apartment rentals, and current residents who live at the apartment building. Key design element will be incorporating the company logo, however, the logo cannot dominate. The building name and manager name are more important than the logo. Current business card design leaves little room for copy, so we may need to reduce the size on the current card to allow for more space for copy.

Target Market(s)

Adults 18-65 years of age, who are looking for an apartment rental, plus current residents who live at our apartment buildings.

Industry/Entity Type

Property Management

Contact Information for Business Card

A major design element will be use of the company logo. Important property and manager contact information must be part of the design. The size of the logo will need to be reduced to make room for building and manager contact copy.

Font styles to use
Sans Serif

Colors
3176b5
000000
959595
ffffff

Requirements
Must have
• 1) Incorporate the company logo.
• 2) Use the company colors (dark blue, black/grey, over white).
• 3) FEATURE THE BUILDING NAME
• 4) FEATURE THE MANAGER NAME
• 5) The company name is less important than BUILDING and MANAGER
• 6) Manager contact information
• **SEE ATTACHED CREATIVE BRIEF**
Nice to have
• 1) Back of card logo watermark
• 2) Ability to write notes on back of carfd
Should not have
• Avoid letting the company logo dominate the card, the building name and manager are more important than the company logo.

```html
<!DOCTYPE html>
<html lang="en">
<head>
<meta charset="utf-8">
<title>Harborview Estates Business Card</title>
<link rel="stylesheet" href="https://fonts.googleapis.com/css2?family=Roboto:wght@400;500;700&family=Roboto+Condensed:wght@700&display=swap">
<style>
  :root {
    --backdrop: #2b2b2b;
    --card-white: #f4f4f4;
    --brand-blue: #0f6aa8;
    --brand-grey: #4a4a4a;
    --text-white: #ffffff;
  }
  html, body {
    margin: 0;
    padding: 0;
    width: 1200px;
    height: 960px;
    overflow: hidden;
    background: var(--backdrop);
  }
  .canvas {
    position: relative;
    width: 1200px;
    height: 960px;
  }
  .card {
    position: absolute;
    left: 320px;
    width: 600px;
    box-sizing: border-box;
  }
  .card-front {
    top: 100px;
    height: 350px;
    background: var(--card-white);
    display: flex;
    align-items: center;
    justify-content: center;
  }
  .brand {
    display: flex;
    align-items: center;
    gap: 14px;
    margin-left: 6px;
  }
  .brand-mark {
    width: 26px;
    height: 26px;
    background: var(--brand-blue);
  }
  .brand-name {
    font-family: "Roboto", sans-serif;
    font-weight: 700;
    font-size: 30px;
    letter-spacing: 1px;
    color: var(--brand-blue);
    text-transform: uppercase;
  }
  .card-back {
    top: 493px;
    height: 342px;
    background: var(--brand-blue);
    color: var(--text-white);
    font-family: "Roboto", sans-serif;
    text-align: center;
    padding-top: 84px;
  }
  .manager-name {
    font-family: "Roboto Condensed", sans-serif;
    font-weight: 700;
    font-size: 23px;
    line-height: 28px;
    margin: 0;
  }
  .manager-title {
    font-size: 15px;
    font-weight: 500;
    line-height: 18px;
    margin: 2px 0 0;
  }
  .property {
    margin-top: 14px;
    font-size: 14.5px;
    line-height: 18.5px;
  }
  .property-name {
    font-weight: 700;
  }
  .contact {
    margin-top: 10px;
    font-size: 14px;
    line-height: 19px;
  }
  .website {
    letter-spacing: 1.6px;
  }
</style>
</head>
<body>
  <div class="canvas">
    <section class="card card-front">
      <div class="brand">
        <span class="brand-mark"></span>
        <span class="brand-name">Harborview Estates LLC</span>
      </div>
    </section>

    <section class="card card-back">
      <h1 class="manager-name">Marisol Quintero</h1>
      <p class="manager-title">Resident Manager</p>
      <div class="property">
        <div class="property-name">Bayside Court Apartments</div>
        <div>2845 Cedar Crest Lane</div>
        <div>Port Avila, CA 90210</div>
      </div>
      <div class="contact">
        <div>P.555-210-4480 M.555-318-7702</div>
        <div>F.555-406-1195 E.marisol@harborviewest.com</div>
        <div class="website">www.harborviewest.com</div>
      </div>
    </section>
  </div>
</body>
</html>
```